Business Card Design 2018 Kestrel Machining

Hello,

We need a business card design to reflect our new website we just had designed ( http://www.kestrelmachining.ca/)

We are a growing machine shop looking to grow our clientele and are hoping to update our current business card design to match our website and industry

The colours and design of our website should match to achieve what we are looking for.

I have attached a few images for reference as well as our logo and ISO 9000 needs to be apparent on the card as well

Please let me know what you have :)
Please copy marla@kestrelmachining.ca on all communication regarding this project

Thanks !!!

Industry/Entity Type

Business

Contact Information for Business Card

Company Name, employee name and title and contact details

Colors
f78f20
ffffff
00a990

Requirements
Must have
• Our logo, Iso 9000 same colours as our website http://www.kestrelmachining.ca/

```html
<!DOCTYPE html>
<html lang="en">
<head>
<meta charset="utf-8">
<title>Kestrel Machining — Business Card</title>
<link rel="stylesheet" href="https://fonts.googleapis.com/css2?family=Exo+2:wght@700;800&family=Roboto:wght@400;500&display=swap">
<style>
  :root {
    --backdrop: #e6e3df;
    --card-white: #f6f6f6;
    --teal: #1e939b;
    --teal-light: #3fc4cd;
    --teal-deep: #11969d;
    --ink: #1c1c1c;
    --text-grey: #555a5c;
    --white: #ffffff;
  }
  * { margin: 0; padding: 0; box-sizing: border-box; }
  html, body {
    width: 1200px; height: 960px; overflow: hidden;
    background: var(--backdrop);
  }
  .canvas { position: relative; width: 1200px; height: 960px; }

  .card {
    position: absolute; width: 600px; height: 344px;
    box-shadow: 0 3px 8px rgba(0,0,0,0.28);
  }
  .card--front { left: 314px; top: 113px; background: var(--card-white); }
  .card--back {
    left: 311px; top: 472px; height: 343px;
    background: radial-gradient(ellipse 70% 75% at 50% 42%, var(--teal-light) 0%, #27b0b8 45%, var(--teal-deep) 100%);
  }

  .wordmark {
    position: absolute; display: flex; align-items: center; gap: 10px;
    font-family: "Exo 2", sans-serif; font-weight: 800; letter-spacing: 0.5px;
    text-transform: uppercase; white-space: nowrap;
  }
  .wordmark__square { width: 30px; height: 30px; flex: none; }
  .card--front .wordmark { left: 50px; top: 52px; font-size: 31px; color: var(--ink); }
  .card--front .wordmark__square { background: var(--teal); }
  .card--back .wordmark {
    left: 0; right: 0; top: 140px; justify-content: center;
    font-size: 36px; color: var(--white);
  }
  .card--back .wordmark__square { background: var(--white); width: 34px; height: 34px; }

  .holder { position: absolute; left: 50px; top: 206px; }
  .holder__name {
    font-family: "Exo 2", sans-serif; font-weight: 800; font-size: 21px;
    letter-spacing: 1.5px; color: var(--teal); text-transform: uppercase;
    line-height: 24px;
  }
  .holder__title {
    font-family: "Roboto", sans-serif; font-weight: 500; font-size: 14.5px;
    color: var(--ink); margin-top: 1px;
  }

  .contacts {
    position: absolute; left: 345px; top: 158px; list-style: none;
    font-family: "Roboto", sans-serif; font-size: 14.5px; line-height: 19px;
    color: var(--text-grey); white-space: nowrap;
  }
  .contacts li { display: flex; align-items: flex-start; }
  .contacts li.address { margin-bottom: 8px; }
  .contacts svg { width: 14px; height: 14px; margin: 2px 12px 0 0; flex: none; fill: var(--teal); }

  .badges { position: absolute; top: 25px; right: 27px; display: flex; gap: 14px; }
  .badge { height: 24px; background: var(--white); border-radius: 2px; }
  .badge--quality { width: 82px; }
  .badge--listing { width: 78px; }

  .back-url {
    position: absolute; left: 0; right: 0; top: 287px; text-align: center;
    font-family: "Roboto", sans-serif; font-size: 14px; letter-spacing: 5px;
    color: var(--white);
  }
</style>
</head>
<body>
<main class="canvas">

  <section class="card card--front" aria-label="Business card front">
    <div class="wordmark"><span class="wordmark__square"></span>Kestrel Machining</div>

    <div class="holder">
      <p class="holder__name">Owen Harper</p>
      <p class="holder__title">CEO/FOUNDER</p>
    </div>

    <ul class="contacts">
      <li class="address">
        <svg viewBox="0 0 14 14"><path d="M7 0a4.6 4.6 0 0 0-4.6 4.6C2.4 8 7 14 7 14s4.6-6 4.6-9.4A4.6 4.6 0 0 0 7 0zm0 6.5a1.9 1.9 0 1 1 0-3.8 1.9 1.9 0 0 1 0 3.8z"/></svg>
        <span>2145 Foundry Road<br>Hamilton, Ontario L8N 2K4</span>
      </li>
      <li>
        <svg viewBox="0 0 14 14"><path d="M3 1l2.2 2.8-1.3 1.6c.8 1.8 2.1 3.1 3.8 3.9l1.6-1.3L12.2 10 11 12.6C6 12.4 1.6 8 1.4 3z"/></svg>
        <span>905 318 4472</span>
      </li>
      <li>
        <svg viewBox="0 0 14 14"><path d="M3.5 0h7v14h-7zM4.8 1.5v9.5h4.4V1.5zM6.2 12h1.6v1H6.2z" fill-rule="evenodd"/></svg>
        <span>905 627 1183</span>
      </li>
      <li>
        <svg viewBox="0 0 14 14"><path d="M3.5 1h7v3.5h-7zM0 5.5h14v6H0zM3 9h8v4H3z"/></svg>
        <span>905 318 4479</span>
      </li>
      <li>
        <svg viewBox="0 0 14 14"><path d="M0 3h14v1L7 8 0 4zM0 5.3l7 4 7-4V11H0z"/></svg>
        <span>owen@kestrelmachining.ca</span>
      </li>
      <li>
        <svg viewBox="0 0 14 14"><circle cx="7" cy="7" r="6.5"/><path d="M4 4.5c1.2 0 1.8.8 1.5 1.8-.3.8.6 1.4.2 2.4L4.3 10 3 7.5zM8.5 2.5c.6 1 2 1 2.4 2.4-.8.4-1.8 0-2 1 .4 1.4 1.6 1.6 1.3 3.4L9 11 8 8.5 7 6.5z" fill="#f6f6f6"/></svg>
        <span>www.kestrelmachining.ca</span>
      </li>
    </ul>
  </section>

  <section class="card card--back" aria-label="Business card back">
    <div class="badges">
      <div class="badge badge--quality" role="img" aria-label="Quality certification badge"></div>
      <div class="badge badge--listing" role="img" aria-label="Industry listing badge"></div>
    </div>
    <div class="wordmark"><span class="wordmark__square"></span>Kestrel Machining</div>
    <p class="back-url">www.kestrelmachining.ca</p>
  </section>

</main>
</body>
</html>
```